Commit To Be The Best! - Marketing, Training, Managment for Multifamily Professionals

Flyer for training event. I have to be able to edit location, times, speakers, cost,
We will have 2 to 4 speakers for each event. Each event may have a different topic relating to the main topic (Marketing, Training, Management). The idea is to get as many people to open or pick up the fly and say "I have to attend" this seminar. We are the experts in the industry and want to portray this with the flyer. Each speaker will have a topic and a certain amount of time. Each topic will be different.
Updates

Project Deadline Extended
Reason: I apologize for the new design deadline. I've been traveling extensively for work and unable to view submissions. Currently I am not traveling and able to dedicate time to view all of the wonderful submissions. I'm looking forward to selecting one. Thank you all for your understanding.

Target Market(s)

Multifamily - Apartment Communities, Owners, Apartment Associations, Leasing Agents, Marketing Directors, Managers, Presidents,

Industry/Entity Type

Marketing

Colors

Designer to choose colors to be used in the design.

Requirements
Must have
• Editable flyer. I have to be able to edit; location, times/date, speaker, cost, description.
• Sponsored by KTV Power attached Logo for KTV
Nice to have
• Spot for photo of each speaker (2-4) speaker

```html
<!DOCTYPE html>
<html lang="en">
<head>
<meta charset="utf-8">
<title>Join The Event – Topic: Marketing</title>
<link href="https://fonts.googleapis.com/css2?family=Antonio:wght@100;300;400;700&family=Montserrat:wght@400;600&family=Roboto+Condensed:wght@400;700&display=swap" rel="stylesheet">
<style>
  :root{
    --page:#e9e6e1;
    --navy:#262f45;
    --navy-deep:#1d2538;
    --photo-blue:#2c4f8e;
    --grey:#b9bcc2;
    --magenta:#e0249a;
    --sky:#5fa3e8;
    --yellow:#f5d23d;
    --white:#ffffff;
    --text-soft:#d6dbe6;
  }
  *{box-sizing:border-box;margin:0;padding:0}
  html,body{width:1200px;height:1200px;overflow:hidden;background:var(--page)}
  .flyer{
    position:absolute;left:204px;top:40px;width:792px;height:1120px;
    background:var(--navy);overflow:hidden;
    font-family:"Roboto Condensed",sans-serif;color:var(--white);
    box-shadow:0 10px 30px rgba(0,0,0,.25);
  }
  .crowd-photo{
    position:absolute;left:0;right:0;bottom:0;height:560px;
    background:radial-gradient(ellipse at 62% 40%, #3a63a8 0%, var(--photo-blue) 35%, var(--navy-deep) 80%);
  }
  .pattern{position:absolute;border-radius:2px}
  .pattern--top{
    left:30px;top:60px;width:320px;height:440px;
    background:linear-gradient(135deg, rgba(224,36,154,.55), rgba(245,210,61,.45) 45%, rgba(95,163,232,.5));
  }
  .pattern--bottom{
    right:0;top:740px;width:190px;height:270px;
    background:linear-gradient(135deg, rgba(224,36,154,.55), rgba(245,210,61,.4) 50%, rgba(95,163,232,.5));
  }
  .headline{position:absolute;right:40px;top:30px;text-align:right}
  .headline__join{
    font-family:"Antonio",sans-serif;font-weight:400;font-size:200px;line-height:.85;
    color:var(--grey);letter-spacing:-4px;
  }
  .headline__row{display:flex;justify-content:flex-end;align-items:flex-end;margin-top:6px}
  .headline__the{
    font-family:"Antonio",sans-serif;font-weight:100;font-size:34px;color:var(--grey);
    writing-mode:vertical-rl;transform:rotate(180deg);margin-right:6px;line-height:1;letter-spacing:2px;
  }
  .headline__event{
    font-family:"Antonio",sans-serif;font-weight:100;font-size:118px;line-height:.9;color:var(--magenta);
  }
  .topic{
    position:absolute;right:40px;top:330px;
    font-size:62px;font-weight:700;color:var(--sky);letter-spacing:-1px;
    font-family:"Antonio",sans-serif;
  }
  .description{
    position:absolute;right:40px;top:420px;width:390px;
    font-family:"Montserrat",sans-serif;font-size:11.5px;line-height:1.5;color:var(--text-soft);text-align:justify;
  }
  .speakers{position:absolute;right:40px;top:560px;display:flex;gap:26px}
  .speaker{text-align:center}
  .speaker__photo{
    width:112px;height:112px;border-radius:50%;background:var(--white);
    border:8px solid var(--sky);margin:0 auto 12px;
  }
  .speaker__name{font-family:"Montserrat",sans-serif;font-size:13px;letter-spacing:1px;color:var(--text-soft)}
  .date{position:absolute;left:50px;top:650px;width:320px;font-family:"Antonio",sans-serif;color:var(--grey)}
  .date__day{font-size:120px;font-weight:400;line-height:1}
  .date__day sup{font-size:56px;vertical-align:top;position:relative;top:8px}
  .date__weekday{
    position:absolute;left:150px;top:82px;font-family:"Montserrat",sans-serif;font-weight:600;
    font-size:20px;letter-spacing:2px;color:var(--sky)
  }
  .date__month{font-size:50px;font-weight:100;line-height:1;margin-top:0;letter-spacing:1px}
  .time{
    position:absolute;left:50px;top:826px;background:var(--magenta);
    font-family:"Antonio",sans-serif;font-weight:700;font-size:48px;line-height:1.1;padding:4px 16px;
  }
  .venue{
    position:absolute;left:50px;top:900px;color:var(--yellow);font-style:normal;
    font-family:"Antonio",sans-serif;font-weight:400;font-size:34px;line-height:1.12;
  }
  .venue span{display:block;white-space:nowrap}
  .tickets{position:absolute;left:50px;bottom:28px}
  .tickets__line{font-size:26px;line-height:1.15;color:var(--sky);margin-bottom:4px;white-space:nowrap}
  .tickets__contact{
    display:inline-flex;gap:14px;background:var(--magenta);padding:3px 12px;
    font-size:15px;color:var(--white);white-space:nowrap;
  }
  .price{position:absolute;right:215px;top:800px;text-align:right}
  .price__amount{font-family:"Antonio",sans-serif;font-weight:700;font-size:96px;line-height:1;color:var(--grey)}
  .price__note{font-family:"Montserrat",sans-serif;font-size:15px;line-height:1.2;margin-top:8px;letter-spacing:1px;color:var(--yellow)}
  .sponsor{position:absolute;right:50px;bottom:40px;display:flex;align-items:center;gap:12px}
  .sponsor__label{font-size:18px;color:var(--white)}
  .sponsor__box{
    background:var(--white);padding:14px 20px;display:flex;align-items:center;gap:8px;
  }
  .sponsor__name{font-family:"Roboto Condensed",sans-serif;font-weight:700;font-size:34px;color:var(--navy);line-height:1}
  .sponsor__dot{width:12px;height:12px;background:var(--magenta)}
</style>
</head>
<body>
<main class="flyer">
  <div class="crowd-photo" role="img" aria-label="Blurred photo of attendees at a seminar, in blue tones"></div>
  <div class="pattern pattern--top" role="img" aria-label="Decorative pattern of coloured crossing bars"></div>
  <div class="pattern pattern--bottom" role="img" aria-label="Decorative pattern of coloured crossing bars"></div>

  <header class="headline">
    <div class="headline__join">JOIN</div>
    <div class="headline__row">
      <span class="headline__the">THE</span>
      <span class="headline__event">EVENT</span>
    </div>
  </header>

  <h2 class="topic">Topic:MARKETING</h2>
  <p class="description">Join leading multifamily marketers for an evening of practical sessions on leasing strategy, resident retention and digital outreach. Each speaker brings a focused topic and proven tools you can use the very next morning. Connect with owners, managers and association leaders, compare notes on what works today, and leave with a clear plan to grow occupancy and strengthen your team across every community you serve.</p>

  <section class="speakers">
    <div class="speaker"><div class="speaker__photo"></div><div class="speaker__name">SPEAKER 1</div></div>
    <div class="speaker"><div class="speaker__photo"></div><div class="speaker__name">SPEAKER 2</div></div>
    <div class="speaker"><div class="speaker__photo"></div><div class="speaker__name">SPEAKER 3</div></div>
  </section>

  <section class="date">
    <div class="date__day">21<sup>ST</sup></div>
    <div class="date__weekday">SATURDAY</div>
    <div class="date__month">OCTOBER 2017</div>
  </section>
  <div class="time">9PM - 2:30AM</div>
  <address class="venue"><span>HARBORVIEW HALL 1480 N</span><span>Lakeside Dr,</span><span>Chicago, IL 60611</span></address>

  <footer class="tickets">
    <div class="tickets__line">Get Tickets At: www.seatpass.com</div>
    <div class="tickets__contact"><span>312-555-0148</span><span>events@commitbest.com</span><span>www.ktvpower.com</span></div>
  </footer>

  <div class="price">
    <div class="price__amount">$50</div>
    <div class="price__note">PER ENTRY</div>
  </div>

  <div class="sponsor">
    <span class="sponsor__label">Sponsored by</span>
    <div class="sponsor__box"><span class="sponsor__name">KTV</span><span class="sponsor__dot"></span></div>
  </div>
</main>
</body>
</html>
```